New LLC consulting company needs a business card design

I need a business card design for new company in Alexandria Virginia called TK Verdane Consulting LLC. The company is focused on consulting for defense and national security issues with expertise in nuclear and space topics. I would like to see designs that are simple and I am open to colors except for brown.

Target Market(s)

All businesses that are seeking consulting help

Industry/Entity Type

Consulting

Contact Information for Business Card

Name of company - TK Verdane Consulting LLC; name (Delia Pratt) President; email: prattdq47@mailvessa.com; Phone: 703-555-0142

Requirements
Must have
• The details described above
Nice to have
• I'm open to all ideas
Should not have
• No brown

```html
<!DOCTYPE html>
<html lang="en">
<head>
<meta charset="utf-8">
<title>Delia Pratt — TK Verdane Consulting LLC</title>
<link href="https://fonts.googleapis.com/css2?family=Montserrat:wght@400;600&display=swap" rel="stylesheet">
<style>
  :root {
    --backdrop: #999999;
    --card: #1a1a1a;
    --ink: #ffffff;
  }
  html, body {
    margin: 0;
    padding: 0;
    width: 1200px;
    height: 1059px;
    overflow: hidden;
    background: var(--backdrop);
  }
  .card {
    position: absolute;
    left: 234px;
    top: 320px;
    width: 732px;
    height: 419px;
    border-radius: 25px;
    background: var(--card);
    font-family: "Montserrat", sans-serif;
    color: var(--ink);
  }
  .card__frame {
    position: absolute;
    left: 26px;
    top: 26px;
    right: 26px;
    bottom: 26px;
    border: 1px solid var(--ink);
  }
  .identity {
    position: absolute;
    right: 421px;
    text-align: right;
    line-height: 1;
    white-space: nowrap;
  }
  .identity__name {
    top: 175px;
    font-size: 36px;
    font-weight: 600;
  }
  .identity__role {
    top: 223px;
    font-size: 19px;
    font-weight: 400;
    letter-spacing: 0.3px;
  }
  .divider {
    position: absolute;
    left: 347px;
    top: 174px;
    width: 2px;
    height: 73px;
    background: var(--ink);
  }
  .contact {
    position: absolute;
    left: 386px;
    display: flex;
    align-items: center;
    gap: 8px;
    font-size: 18px;
    font-weight: 400;
    letter-spacing: 0.3px;
    line-height: 1;
    white-space: nowrap;
  }
  .contact--email { top: 186px; }
  .contact--phone { top: 219px; }
  .contact__icon {
    width: 16px;
    height: 16px;
    flex: none;
    fill: var(--ink);
  }
  .company {
    position: absolute;
    left: 0;
    right: 0;
    top: 330px;
    text-align: center;
    font-size: 14px;
    font-weight: 400;
    letter-spacing: 3px;
    text-transform: uppercase;
    line-height: 1;
    white-space: nowrap;
  }
</style>
</head>
<body>
  <div class="card">
    <div class="card__frame"></div>

    <div class="identity identity__name">Delia Pratt</div>
    <div class="identity identity__role">President</div>

    <div class="divider"></div>

    <div class="contact contact--email">
      <svg class="contact__icon" viewBox="0 0 16 16" aria-hidden="true">
        <path d="M1 3.5h14v1.2L8 9 1 4.7z"/>
        <path d="M1 6.2l4.6 2.9L1 12.6z M15 6.2l-4.6 2.9 4.6 3.5z M6.6 9.7L8 10.6l1.4-.9 5.3 4H1.3z"/>
      </svg>
      <span>prattdq47@mailvessa.com</span>
    </div>

    <div class="contact contact--phone">
      <svg class="contact__icon" viewBox="0 0 16 16" aria-hidden="true">
        <path d="M3.3 1.2l2.2 2.6c.3.4.3.9 0 1.2L4.4 6.1c.8 2 2.3 3.6 4.3 4.5l1.1-1.1c.4-.3.9-.3 1.2 0l2.6 2.2c.4.3.4.9.1 1.2l-1.3 1.4c-.6.6-1.5.8-2.3.5C5.8 13.4 2.7 10.3 1.4 6c-.3-.8-.1-1.7.5-2.3L3.1 1.2c.1-.1.1 0 .2 0z"/>
        <path d="M9 1.5a5.6 5.6 0 0 1 5.5 5.5h-1.2A4.4 4.4 0 0 0 9 2.7z M9 4a3 3 0 0 1 3 3h-1.2A1.8 1.8 0 0 0 9 5.2z"/>
      </svg>
      <span>703-555-0142</span>
    </div>

    <div class="company">TK Verdane Consulting LLC</div>
  </div>
</body>
</html>
```